Allied Health team of Physiotherapists & Occupational Therapists seek a business card design

We have our new logo, we now need our new business cards and stationary. Tidewell: Oedema & Family Clinic is seeking a generic card design to represent our whole team and individual cards for each therapist that incorporates our new logo to communicate our holistic approach that is calming, nuturing, supportive and welcoming.
Our Physiotherapists and Occupational Therapists assess, treat and provide education for people who are at risk of or who have lymphoedema. This is often as a result of treatment for cancer. We provide pre-operative and post-operative management and cancer rehabilitation in our Pilates studio. Our team also consists of Physiotherapists who have a strong interest in pelvic floor and continence management for both men and women.

Target Market(s)

Mainly women health conscious

Industry/Entity Type

Allied Health: Physiotherapy / Occupational Therapy

Contact Information for Business Card

Address: 14 Gallivant Ave Harbourne 3412 Phone: 84316570 fax: 8431 6578 Email: info@tidewellcareservices.com.au Website: tidewellcareservices.com.au Facebook address: facebook.com/TidewellOedemaAndFamilyCareClinic. Room to write appointments. Individual cards need to have name, office email and individual email and professional details

Requirements
Must have
• Logo as per uploaded documents

```html
<!DOCTYPE html>
<html lang="en">
<head>
<meta charset="utf-8">
<title>Tidewell business cards</title>
<link href="https://fonts.googleapis.com/css2?family=Jost:wght@400;500&family=Lato:ital,wght@1,700&display=swap" rel="stylesheet">
<style>
:root{
  --stage:#131416;
  --cream:#fefbd8;
  --ink:#2b2b2b;
  --peach:#f5a07f;
  --peach-light:#f9b795;
  --peach-deep:#f3937a;
  --white:#ffffff;
}
*{margin:0;padding:0;box-sizing:border-box}
html,body{width:1200px;height:886px;overflow:hidden;background:var(--stage)}
.canvas{position:relative;width:1200px;height:886px}
.card{position:absolute;width:447px;height:255px;font-family:"Jost",sans-serif}
.card--front{left:223px;top:141px;background:var(--cream);color:var(--ink)}
.card--back{left:530px;top:488px;background:linear-gradient(90deg,var(--peach-light),var(--peach-deep));color:var(--white)}

.therapist{position:absolute;right:16px;top:34px;text-align:right}
.therapist__name{font-family:"Lato",sans-serif;font-style:italic;font-weight:700;font-size:26px;line-height:1}
.therapist__role{font-size:12px;margin-top:6px}

.credentials{position:absolute;left:20px;top:96px;list-style:none;font-size:10.5px;line-height:15px}
.credentials li{position:relative;padding-left:10px}
.credentials li::before{content:"";position:absolute;left:0;top:5px;width:5px;height:5px;border-radius:50%;background:var(--peach)}

.services{position:absolute;left:16px;top:195px;font-size:10.5px;font-weight:500;line-height:15px}

.clinic-mark{position:absolute;display:flex;align-items:center;justify-content:center;border-radius:50%;font-weight:400}
.card--front .clinic-mark{left:297px;top:120px;width:122px;height:122px;border:1.5px solid var(--peach);color:var(--peach);font-size:24px}
.card--back .clinic-mark{left:309px;top:31px;width:106px;height:106px;border:1.5px solid var(--white);color:var(--white);font-size:21px}

.contacts{position:absolute;left:17px;top:101px;list-style:none;font-size:12px;line-height:17px}
.contacts li{display:flex;align-items:center;gap:6px}
.contacts svg{width:12px;height:12px;flex:none}
.contacts .phone-number{font-size:13px;letter-spacing:1.2px}

.appointment{position:absolute;left:241px;top:226px;font-size:12px;display:flex;align-items:baseline;gap:4px}
.appointment__line{width:92px;border-bottom:1px dotted var(--white);height:1px}
</style>
</head>
<body>
<div class="canvas">
  <section class="card card--front">
    <div class="therapist">
      <h1 class="therapist__name">Maren Ashby</h1>
      <p class="therapist__role">Physiotherapist</p>
    </div>
    <ul class="credentials">
      <li>B. Physio (Hons), B.App.Sci.<br>(Human Movement/Psych)</li>
      <li>Post Grad Certif. Exercise for Women</li>
      <li>Post Grad Certif. Continence &amp; Pelvic<br>Floor Rehabilitation</li>
    </ul>
    <p class="services">Lymphoedema &amp; Oncology Rehabilitation<br>Continence &amp; Pelvic Floor</p>
    <div class="clinic-mark">Tidewell</div>
  </section>

  <section class="card card--back">
    <ul class="contacts">
      <li><svg viewBox="0 0 12 12" fill="none" stroke="currentColor" stroke-width="0.9"><circle cx="6" cy="6" r="5.4"/><path d="M4 3.2l1 1.4-.6.7a4 4 0 0 0 2.3 2.3l.7-.6 1.4 1-.6 1C6 9 3 6 3.2 3.8z"/></svg><span class="phone-number">8431 6570</span></li>
      <li><svg viewBox="0 0 12 12" fill="none" stroke="currentColor" stroke-width="0.9"><circle cx="6" cy="6" r="5.4"/><rect x="3.5" y="4.5" width="5" height="3.5"/><path d="M4.5 4.5V3h3v1.5"/></svg><span class="phone-number">8431 6578</span></li>
      <li><svg viewBox="0 0 12 12" fill="none" stroke="currentColor" stroke-width="0.9"><circle cx="6" cy="6" r="5.4"/><rect x="3.2" y="4" width="5.6" height="4"/><path d="M3.2 4l2.8 2.2L8.8 4"/></svg><span>info@tidewellcareservices.com.au</span></li>
      <li><svg viewBox="0 0 12 12" fill="none" stroke="currentColor" stroke-width="0.9"><circle cx="6" cy="6" r="5.4"/></svg><span>TidewellOedemaAndFamilyCareClinic</span></li>
      <li><svg viewBox="0 0 12 12" fill="none" stroke="currentColor" stroke-width="0.9"><circle cx="6" cy="6" r="5.4"/><circle cx="6" cy="6" r="3"/><path d="M3 6h6"/></svg><span>tidewellcareservices.com.au</span></li>
      <li><svg viewBox="0 0 12 12" fill="none" stroke="currentColor" stroke-width="0.9"><circle cx="6" cy="6" r="5.4"/><path d="M6 9.2S3.8 6.8 3.8 5.2a2.2 2.2 0 0 1 4.4 0C8.2 6.8 6 9.2 6 9.2z"/><circle cx="6" cy="5.2" r="0.8"/></svg><span>14 Gallivant Ave, Harbourne 3412</span></li>
    </ul>
    <div class="clinic-mark">Tidewell</div>
    <p class="appointment">Next Appointment <span class="appointment__line"></span></p>
  </section>
</div>
</body>
</html>
```